One of a Kind Clean Business Card

We need to design a new business card template for our company. Our company designs and produced merchandising displays. You can see a sample of what we produce on our site www.qorvanexhibits.net. I have uploaded our logo in vector format, as well as a picture of our current business cards. We want a totally different look. We want simple and clean, looking forward to seeing what people create.
Updates

I would like to update the address for Qorvan Display Group Inc. 518 E Tollmere Ln Arlington Heights, IL 60017 Would also note. No QR codes

Industry/Entity Type

Business

Contact Information for Business Card

Need a 1 sided business card designed.

Font styles to use
Serif

Requirements
Must have
• Easy to view; Clean Design
Nice to have
• Features that promote engineering and creativity
Should not have
• Too much clutter, keep it simple

```html
<!DOCTYPE html>
<html lang="en">
<head>
<meta charset="utf-8">
<title>Qorvan Display Group Inc. – Business Card</title>
<link rel="stylesheet" href="https://fonts.googleapis.com/css2?family=Source+Sans+3:wght@300;400;600&display=swap">
<style>
  :root {
    --stage: #e9e7e3;
    --paper: #f7f7f5;
    --ink: #1a1a1a;
    --band: #111111;
    --accent: #b3202f;
    --light-text: #f2f2f2;
  }
  * { box-sizing: border-box; margin: 0; padding: 0; }
  html, body {
    width: 1200px; height: 1022px; overflow: hidden;
    background: var(--stage);
    font-family: "Source Sans 3", "Helvetica Neue", Arial, sans-serif;
  }
  .stage {
    width: 1200px; height: 1022px;
    display: flex; align-items: center; justify-content: center;
  }
  .card {
    position: relative;
    width: 900px; height: 514px;
    background: var(--paper);
    box-shadow: 0 18px 40px rgba(0,0,0,.18);
    overflow: hidden;
  }
  .brand {
    position: absolute; left: 60px; bottom: 150px;
    width: 400px;
  }
  .brand-name {
    font-size: 30px; font-weight: 300; line-height: 1.2;
    color: var(--ink);
  }
  .band {
    position: absolute; top: 0; right: 0; bottom: 0;
    width: 410px;
    background: var(--band);
    color: var(--light-text);
  }
  .corner-marks {
    position: absolute; top: 0; right: 22px;
    display: flex; gap: 6px;
  }
  .corner-marks span {
    width: 16px; height: 12px; background: var(--paper);
  }
  .identity {
    position: absolute; top: 48px; right: 44px;
    text-align: right;
  }
  .person-name {
    font-size: 28px; font-weight: 600; color: var(--accent);
    margin-bottom: 20px;
  }
  .address {
    font-size: 20px; font-weight: 300; line-height: 1.4;
  }
  .contacts {
    position: absolute; left: 40px; bottom: 46px;
    list-style: none;
  }
  .contacts li {
    display: flex; align-items: center; gap: 16px;
    font-size: 20px; font-weight: 300; line-height: 1.6;
  }
  .contacts svg { width: 18px; height: 18px; flex: none; }
  .contacts svg * { fill: none; stroke: var(--accent); stroke-width: 2; }
  .contacts svg .solid { fill: var(--accent); stroke: none; }
</style>
</head>
<body>
<main class="stage">
  <article class="card">
    <div class="brand">
      <p class="brand-name">Qorvan Display Group Inc.</p>
    </div>

    <section class="band">
      <div class="corner-marks"><span></span><span></span></div>

      <div class="identity">
        <h1 class="person-name">Dana Welkers</h1>
        <p class="address">518 E Tollmere Ln<br>Arlington Heights, IL 60017</p>
      </div>

      <ul class="contacts">
        <li>
          <svg viewBox="0 0 20 20" aria-hidden="true"><path class="solid" d="M5 2l3 4-2 2c1 3 3 5 6 6l2-2 4 3-2 3C9 18 2 11 2 4z"/></svg>
          815-555-0142
        </li>
        <li>
          <svg viewBox="0 0 20 20" aria-hidden="true"><rect x="3" y="4" width="14" height="12" rx="1"/></svg>
          312-555-0176
        </li>
        <li>
          <svg viewBox="0 0 20 20" aria-hidden="true"><rect class="solid" x="2" y="4" width="16" height="12"/><path d="M2 4l8 7 8-7" style="stroke:#111"/></svg>
          dwelkers@qorvanexhibits.net
        </li>
        <li>
          <svg viewBox="0 0 20 20" aria-hidden="true"><circle cx="10" cy="10" r="8"/><path d="M2 10h16M10 2c-4 4-4 12 0 16M10 2c4 4 4 12 0 16"/></svg>
          www.qorvanexhibits.net
        </li>
      </ul>
    </section>
  </article>
</main>
</body>
</html>
```